Whitcombe Business Card Design

The name of the business is Dario Whitcombe, CPA LLC
The service that we offer is Accounting, Tax & Consulting Services. I need it to have the following items:
Dario Whitcombe, Principal
Phone Number
Email Address
Physical Address

I have attached the company logo, one in black and one in white. Please provide a design in black background and the other in white background. Please include "Accounting, Tax & Consulting Services". I want the business card to be clean and very professional.

```html
<!DOCTYPE html>
<html lang="en">
<head>
<meta charset="UTF-8">
<title>Dario Whitcombe, CPA LLC — Business Cards</title>
<link href="https://fonts.googleapis.com/css2?family=Montserrat:wght@400;500;600;700&display=swap" rel="stylesheet">
<style>
  :root {
    --stage: #2b2b2b;
    --card-dark: #0c0c0c;
    --card-light: #ffffff;
    --brand-red: #9b1b1f;
    --ink: #2e2e2e;
    --muted: #8a8a8a;
    --rule-dark: #6a6a6a;
    --faint: #f0f1f1;
    --white: #ffffff;
  }
  * { box-sizing: border-box; margin: 0; padding: 0; }
  html, body {
    width: 1200px; height: 1024px; overflow: hidden;
    background: var(--stage);
    font-family: "Montserrat", sans-serif;
  }
  .stage {
    width: 1200px; height: 1024px;
    display: flex; flex-direction: column; align-items: center; justify-content: center;
    gap: 40px;
  }
  .card {
    width: 800px; height: 457px; position: relative; overflow: hidden;
    box-shadow: 0 10px 30px rgba(0,0,0,.45);
  }

  /* Front: dark */
  .card--front { background: var(--card-dark); color: var(--white); }
  .front-brand {
    position: absolute; top: 120px; left: 0; right: 0; text-align: center;
  }
  .front-brand .mark-square {
    display: inline-block; width: 22px; height: 22px; background: var(--brand-red);
    vertical-align: middle; margin-right: 12px;
  }
  .front-brand .firm-name {
    display: inline-block; vertical-align: middle;
    font-weight: 600; font-size: 34px; letter-spacing: 1px; color: var(--white);
  }
  .front-brand .designation {
    margin-top: 14px; font-weight: 600; font-size: 19px; letter-spacing: 3px;
  }
  .front-services {
    position: absolute; top: 262px; left: 0; right: 0; text-align: center;
  }
  .front-services .service-line {
    display: flex; align-items: center; justify-content: center; gap: 14px;
    font-size: 15px; letter-spacing: 2px; font-weight: 500;
  }
  .front-services .service-line::before,
  .front-services .service-line::after {
    content: ""; width: 120px; height: 1px; background: var(--rule-dark);
  }
  .front-services .service-sub {
    margin-top: 8px; font-size: 15px; letter-spacing: 2px; font-weight: 500;
  }
  .front-rule {
    position: absolute; left: 0; right: 0; top: 340px; height: 1px; background: var(--rule-dark);
  }

  /* Back: light */
  .card--back { background: var(--card-light); color: var(--ink); }
  .back-accent {
    position: absolute; right: 40px; top: 60px; width: 300px; height: 300px;
    background: var(--faint);
  }
  .back-brand { position: absolute; left: 60px; top: 70px; }
  .back-brand .firm-name {
    font-weight: 600; font-size: 22px; color: var(--ink); letter-spacing: .5px;
  }
  .back-brand .designation {
    margin-top: 6px; font-weight: 500; font-size: 12px; letter-spacing: 2.5px; color: var(--muted);
  }
  .person { position: absolute; left: 60px; top: 190px; }
  .person .person-name {
    font-weight: 700; font-size: 34px; color: var(--brand-red); letter-spacing: .5px;
  }
  .person .person-role { font-size: 19px; color: var(--muted); margin-top: 2px; }
  .contact { position: absolute; left: 60px; top: 300px; list-style: none; }
  .contact li {
    display: flex; align-items: flex-start; gap: 10px;
    font-size: 17px; color: var(--muted); line-height: 1.45; margin-bottom: 2px;
  }
  .contact .icon { width: 18px; height: 18px; flex: none; margin-top: 4px; }
  .contact .icon-spacer { width: 18px; flex: none; }
</style>
</head>
<body>
<main class="stage">
  <section class="card card--front" aria-label="Business card front">
    <div class="front-brand">
      <span class="mark-square"></span><span class="firm-name">DARIO WHITCOMBE, CPA LLC</span>
      <p class="designation">CERTIFIED PUBLIC ACCOUNTANT</p>
    </div>
    <div class="front-services">
      <p class="service-line">ACCOUNTING</p>
      <p class="service-sub">TAX &amp; CONSULTING SERVICES</p>
    </div>
    <div class="front-rule"></div>
  </section>

  <section class="card card--back" aria-label="Business card back">
    <div class="back-accent"></div>
    <div class="back-brand">
      <p class="firm-name">DARIO WHITCOMBE, CPA LLC</p>
      <p class="designation">CERTIFIED PUBLIC ACCOUNTANT</p>
    </div>
    <div class="person">
      <p class="person-name">DARIO WHITCOMBE</p>
      <p class="person-role">Principal</p>
    </div>
    <ul class="contact">
      <li>
        <svg class="icon" viewBox="0 0 18 18" aria-hidden="true">
          <circle cx="9" cy="9" r="9" fill="var(--brand-red)"/>
          <path d="M6 5.2c.4-.3.9-.2 1.1.2l.7 1.3c.2.4.1.8-.2 1l-.5.4c.4.9 1.1 1.6 2 2l.4-.5c.3-.3.7-.4 1-.2l1.3.7c.4.2.5.7.2 1.1l-.5.6c-.4.5-1.2.6-1.8.3-1.9-.9-3.3-2.3-4.2-4.2-.3-.6-.2-1.4.3-1.8z" fill="#fff"/>
        </svg>
        <span>(555) 214-0736</span>
      </li>
      <li>
        <svg class="icon" viewBox="0 0 18 18" aria-hidden="true">
          <circle cx="9" cy="9" r="9" fill="var(--brand-red)"/>
          <rect x="4.5" y="6" width="9" height="6.5" rx=".8" fill="#fff"/>
          <path d="M4.8 6.4 9 9.6l4.2-3.2" stroke="var(--brand-red)" stroke-width="1" fill="none"/>
        </svg>
        <span>info@dariowhitcombe.com</span>
      </li>
      <li>
        <span class="icon-spacer"></span>
        <span>123, Your Street Name, your<br>city, lane 00125</span>
      </li>
    </ul>
  </section>
</main>
</body>
</html>
```